We are a recruitment company based in Norwich/Cambridge England.
I have included our company logo which we want to remain the same.

What we are looking for is a new creative Business card which will really stand out!!

Contact Information for Business Card

Harriet Dunmore
email: Harriet@plavex.co.uk
Address: Brackwell House
Fenmoor Enterprise Park
Partridge Way
Norwich
QB9 3KX
Tel:01632 960418

```html
<!DOCTYPE html>
<html lang="en">
<head>
<meta charset="utf-8">
<title>Plavex Business Card</title>
<link href="https://fonts.googleapis.com/css2?family=Jost:wght@400;500;600&display=swap" rel="stylesheet">
<style>
  :root {
    --canvas-bg: #3a3a3a;
    --card-bg: #1c1c1c;
    --accent: #8cc63f;
    --grey: #8e8e90;
    --text: #e9e9e9;
  }
  * { margin: 0; padding: 0; box-sizing: border-box; }
  html, body {
    width: 1200px; height: 800px; overflow: hidden;
    background: var(--canvas-bg);
    font-family: "Jost", sans-serif;
  }
  .stage { position: relative; width: 1200px; height: 800px; }
  .card {
    position: absolute; width: 540px; height: 310px;
    background: var(--card-bg); overflow: hidden;
    box-shadow: 0 10px 30px rgba(0,0,0,.45);
  }
  .card--front { left: 110px; top: 70px; }
  .card--back { left: 560px; top: 420px; }

  .brand { display: flex; align-items: center; gap: 12px; }
  .brand__dot { width: 26px; height: 26px; border-radius: 50%; background: var(--accent); }
  .brand__name { font-size: 44px; font-weight: 500; color: var(--text); line-height: 1; letter-spacing: -.5px; }
  .brand__tagline {
    font-size: 8px; letter-spacing: 2.6px; color: var(--grey);
    margin-left: 38px; margin-top: 2px;
  }

  .card--front .brand-block { position: absolute; left: 148px; top: 100px; }
  .front__web {
    position: absolute; left: 0; right: 0; top: 240px;
    text-align: center; font-size: 15px; letter-spacing: 1.2px; color: var(--text);
  }
  .web__name { color: var(--accent); }

  .card--back .brand-block { position: absolute; left: 28px; top: 30px; }
  .card--back .brand__name { font-size: 38px; }
  .card--back .brand__dot { width: 22px; height: 22px; }
  .side-tab {
    position: absolute; right: -10px; top: 26px; width: 22px; height: 40px;
    border-radius: 10px; background: var(--accent);
  }
  .person { position: absolute; right: 40px; top: 72px; text-align: right; }
  .person__name { font-size: 26px; font-weight: 600; color: var(--grey); line-height: 1; }
  .person__surname { color: var(--accent); }
  .person__role { font-size: 13px; font-weight: 500; color: var(--text); margin-top: 4px; }
  .divider {
    position: absolute; left: 28px; top: 137px; width: 310px; height: 1.5px;
    background: var(--accent);
  }
  .address {
    position: absolute; right: 34px; top: 150px; text-align: right;
    font-size: 12.5px; line-height: 1.35; color: var(--text);
  }
  .contacts { position: absolute; left: 30px; top: 152px; list-style: none; }
  .contacts li {
    display: flex; align-items: center; gap: 10px;
    font-size: 15px; color: var(--text); line-height: 1.45; letter-spacing: .3px;
  }
  .contacts svg { width: 13px; height: 13px; flex: none; }
  .bottom-bands { position: absolute; left: 0; bottom: 0; width: 540px; height: 70px; }
</style>
</head>
<body>
<main class="stage">

  <section class="card card--front">
    <div class="brand-block">
      <div class="brand">
        <span class="brand__dot"></span>
        <span class="brand__name">Plavex</span>
      </div>
      <p class="brand__tagline">Technology Recruitment</p>
    </div>
    <p class="front__web">www.<span class="web__name">plavexrecruit</span>.com</p>
  </section>

  <section class="card card--back">
    <div class="brand-block">
      <div class="brand">
        <span class="brand__dot"></span>
        <span class="brand__name">Plavex</span>
      </div>
      <p class="brand__tagline">Technology Recruitment</p>
    </div>

    <span class="side-tab"></span>

    <div class="person">
      <p class="person__name">Harriet <span class="person__surname">Dunmore</span></p>
      <p class="person__role">Ceo &amp; Founder</p>
    </div>

    <span class="divider"></span>

    <p class="address">Brackwell House Fenmoor Enterprise Park,<br>Partridge Way Norwich, QB9 3KX</p>

    <ul class="contacts">
      <li>
        <svg viewBox="0 0 16 16"><path fill="#8cc63f" d="M3.5 1.5l2.5 0 1 3.5-1.8 1.2a8 8 0 0 0 4.6 4.6L11 9l3.5 1v2.5c0 1-1 2-2 2C6.5 14.5 1.5 9.5 1.5 3.5c0-1 1-2 2-2z"/></svg>
        01632 960418
      </li>
      <li>
        <svg viewBox="0 0 16 16"><rect x="1" y="3" width="14" height="10" fill="#8cc63f"/><path d="M1 3l7 6 7-6" fill="none" stroke="#1c1c1c" stroke-width="1.4"/></svg>
        Harriet@plavex.co.uk
      </li>
      <li>
        <svg viewBox="0 0 16 16"><circle cx="9" cy="7" r="5" fill="none" stroke="#8cc63f" stroke-width="2"/><path d="M5.5 10.5L1.5 14.5" stroke="#8cc63f" stroke-width="2.2"/></svg>
        <span>www.<span class="web__name">plavexrecruit</span>.com</span>
      </li>
    </ul>

    <svg class="bottom-bands" viewBox="0 0 540 70" preserveAspectRatio="none" aria-hidden="true">
      <path d="M0 46 L392 46 Q400 46 406 40 L414 30 L540 30" fill="none" stroke="#8e8e90" stroke-width="3"/>
      <path d="M0 54 L398 54 Q408 54 414 46 L422 36 Q428 28 440 28 L540 28 L540 70 L0 70 Z" fill="#8cc63f"/>
    </svg>
  </section>

</main>
</body>
</html>
```